International oil and gas consultancy business needs a web design

Hello, I need a web design for a new oil and gas auditing consultancy business. My business undertakes contract audit assignments to review past costs of oil and gas operations (see attached Excel file for more details of the businesses services). I need the design to give the impression of a professional consultancy style of business, rather than a retail style of website. Note: this job is for LAYOUT DESIGN ONLY and not coding / development work.
The following are my key design principles:
1. BASIC DESIGN: I am after a simple and static web design. I don't want the pages busy or cluttered with too many images or detail.
2. HORIZONTAL TABS: I require a horizontal set of tabs towards the top of the screens (see Excel file) which remain in the same position on every page.
3. META TAG PLANNING: The design should allow for effective positioning of content so that key meta tag words can easily be built during the technical build stage.
4. NUMBER OF PAGES: The site will eventually have a maximum of 10 pages. Seven of the pages will reside under the tabs. Can you please present your opening submission for the first two page.
5. USE OF MY LOGO: The attached logo (JPEG file) should be used throughout the website. Please don't change the shape and colour.
6. COLOUR SCHEMES: Can you please consider any of the 3 colour schemes below:
A - dark red (to match the logo), light grey and perhaps another of your liking;
B - dark red (to match the logo), light cream and perhaps another of your liking;
C - dark red (to match the logo), white and perhaps another of your liking.
7. WORD CONTENT: I have attached an Excel file which shows the estimated word content for each page.
8. FUTURE USE OF DESIGN: I'm planning on building a Wordpress website. Can you please ensure the layout design supports this application.

Target Market(s)

oil and gas companies (small and large)

Industry/Entity Type

Oil And Gas

Font styles to use
Sans Serif

Requirements
Nice to have
• The KRL logo and business name should ideally be next to each other. Also, the logo and name should be part of the background graphics, not above it.

```html
<!DOCTYPE html>
<html lang="en">
<head>
<meta charset="utf-8">
<title>Keyline Resource Audits</title>
<link rel="stylesheet" href="https://fonts.googleapis.com/css2?family=Roboto:wght@300;400;500;700&display=swap">
<style>
  :root {
    --brand-red: #8e1a1f;
    --brand-red-dark: #6e1216;
    --heading-red: #9b1c22;
    --text-grey: #444;
    --band-light: #eef0f3;
    --footer-dark: #333333;
    --arc-rose: #d9a5a8;
    --arc-peach: #f4c7b0;
  }
  * { box-sizing: border-box; margin: 0; padding: 0; }
  html, body { width: 973px; height: 1200px; overflow: hidden; }
  body { font-family: "Roboto", sans-serif; background: #fff; color: var(--text-grey); position: relative; }

  .site-header { position: absolute; top: 0; left: 0; width: 973px; height: 113px; }
  .brand { position: absolute; left: 86px; top: 30px; }
  .brand-name { font-size: 40px; font-weight: 700; color: var(--brand-red); letter-spacing: 2px; line-height: 42px; display: block; padding-left: 2px; }
  .brand-tagline { font-size: 12px; color: #555; display: block; margin-top: 2px; }

  .main-nav { position: absolute; left: 284px; top: 37px; height: 40px; display: flex; border-radius: 4px; overflow: hidden; background: linear-gradient(#9c1f25, var(--brand-red-dark)); box-shadow: 0 1px 2px rgba(0,0,0,.25); }
  .main-nav a { display: block; height: 40px; line-height: 40px; padding: 0 15px; font-size: 12px; color: #fff; text-decoration: none; border-left: 1px solid rgba(0,0,0,.25); }
  .main-nav a.is-current { background: linear-gradient(#f2f2f2, #d8d8d8); color: #555; border-left: none; padding: 0 16px; }

  .hero { position: absolute; left: 0; top: 113px; width: 973px; height: 440px; background: linear-gradient(#3f76b5 0%, #7fa9d4 45%, #c9dcec 72%, #79b3cf 86%, #5aa0c0 100%); }
  .hero-caption { position: absolute; left: 80px; top: 147px; width: 406px; height: 92px; background: rgba(60,66,72,.88); padding: 14px 0 0 15px; color: #fff; }
  .hero-title { font-size: 33px; font-weight: 400; line-height: 36px; }
  .hero-sub { font-size: 16px; font-weight: 300; margin-top: 5px; padding-left: 5px; }
  .hero-dots { position: absolute; left: 931px; top: 27px; display: flex; flex-direction: column; gap: 5px; }
  .hero-dots span { width: 10px; height: 10px; border-radius: 50%; background: #fff; }
  .hero-dots span.is-active { background: var(--brand-red); }

  .welcome { position: absolute; left: 0; top: 560px; width: 973px; height: 162px; background: linear-gradient(#f7f8fa, var(--band-light)); text-align: center; }
  .welcome h1 { font-size: 18px; font-weight: 400; color: var(--heading-red); margin-top: 39px; }
  .welcome p { font-size: 12.4px; line-height: 24px; color: var(--text-grey); margin: 17px auto 0; width: 780px; }

  .services-heading { position: absolute; top: 746px; left: 0; width: 973px; text-align: center; font-size: 18.5px; font-weight: 400; color: var(--heading-red); }

  .service { position: absolute; top: 804px; width: 250px; text-align: center; }
  .service-icon { display: block; margin: 0 auto; }
  .service h2 { font-size: 16.5px; font-weight: 400; color: var(--heading-red); margin-top: 17px; }
  .service p { font-size: 10.5px; line-height: 18px; color: var(--text-grey); margin: 8px auto 0; width: 238px; text-align: justify; text-align-last: center; }
  .read-more { display: inline-block; margin-top: 14px; width: 89px; height: 31px; line-height: 31px; font-size: 12.5px; color: #fff; text-decoration: none; border-radius: 2px; background: linear-gradient(#a2272c, var(--brand-red-dark)); box-shadow: 0 1px 2px rgba(0,0,0,.3); }

  .site-footer { position: absolute; left: 0; top: 1101px; width: 973px; height: 99px; background: var(--footer-dark); color: #fff; font-size: 11.5px; }
  .copyright { position: absolute; left: 84px; top: 42px; }
  .legal { position: absolute; right: 83px; top: 40px; }
  .legal a { color: #fff; text-decoration: none; }
</style>
</head>
<body>
  <header class="site-header">
    <div class="brand">
      <span class="brand-name">KRL</span>
      <span class="brand-tagline">Keyline Resource Audits</span>
    </div>
    <nav class="main-nav">
      <a class="is-current" href="#">Home</a>
      <a href="#">About Us</a>
      <a href="#">Services</a>
      <a href="#">Our Partners</a>
      <a href="#">Approach</a>
      <a href="#">Why Choose Us</a>
      <a href="#">Contact Us</a>
    </nav>
  </header>

  <section class="hero" role="img" aria-label="Photo of an offshore oil platform with cranes under a blue cloudy sky over the sea">
    <div class="hero-caption">
      <div class="hero-title">Keyline Resource Audits</div>
      <div class="hero-sub">Lorem Ipsum is simply dummy text of the printing</div>
    </div>
    <div class="hero-dots"><span class="is-active"></span><span></span><span></span><span></span><span></span></div>
  </section>

  <section class="welcome">
    <h1>WELCOME TO KEYLINE RESOURCE AUDITS</h1>
    <p>Keyline Resource Audits is a Perth (Australia) based firm specialising in providing quality audit services for the oil and gas industry. Our skills and knowledge of oil and gas, along with a deep understanding of business commercial needs, ensures the high quality of our services</p>
  </section>

  <h2 class="services-heading">Keyline Resource Audits specialise in the following services:</h2>

  <article class="service" style="left:78px">
    <svg class="service-icon" width="110" height="110" viewBox="0 0 110 110" aria-hidden="true">
      <path d="M55 2 A53 53 0 0 1 108 55" fill="none" stroke="var(--arc-rose)" stroke-width="4"/>
      <path d="M2 55 A53 53 0 0 0 55 108" fill="none" stroke="var(--arc-rose)" stroke-width="4"/>
      <circle cx="58" cy="56" r="48" fill="var(--brand-red)"/>
      <path d="M58 35 L81 46 L58 57 L35 46 Z" fill="#fff"/>
      <path d="M35 50 L56 60 L56 82 L35 71 Z M60 60 L81 50 L81 71 L60 82 Z" fill="#fff"/>
    </svg>
    <h2>Joint Venture audits</h2>
    <p>Lorem Ipsum is simply dummy text of the printing and typesetting industry. Lorem Ipsum has been the industry's standard dummy text</p>
    <a class="read-more" href="#">Read More</a>
  </article>

  <article class="service" style="left:357px">
    <svg class="service-icon" width="110" height="110" viewBox="0 0 110 110" aria-hidden="true">
      <path d="M55 2 A53 53 0 0 1 108 55" fill="none" stroke="var(--arc-rose)" stroke-width="4"/>
      <path d="M2 55 A53 53 0 0 0 55 108" fill="none" stroke="var(--arc-rose)" stroke-width="4"/>
      <circle cx="58" cy="56" r="48" fill="var(--brand-red)"/>
      <path d="M34 77 L52 58 L60 66 L78 47" fill="none" stroke="#fff" stroke-width="6" stroke-linecap="round" stroke-linejoin="round"/>
      <path d="M68 40 L84 40 L84 56 Z" fill="#fff"/>
    </svg>
    <h2>Contract audits</h2>
    <p>Lorem Ipsum is simply dummy text of the printing and typesetting industry. Lorem Ipsum has been the industry's standard dummy text</p>
    <a class="read-more" href="#">Read More</a>
  </article>

  <article class="service" style="left:638px">
    <svg class="service-icon" width="110" height="110" viewBox="0 0 110 110" aria-hidden="true">
      <path d="M55 2 A53 53 0 0 1 108 55" fill="none" stroke="var(--arc-peach)" stroke-width="4"/>
      <path d="M2 55 A53 53 0 0 0 55 108" fill="none" stroke="var(--arc-peach)" stroke-width="4"/>
      <circle cx="58" cy="56" r="48" fill="var(--brand-red)"/>
      <text x="58" y="50" text-anchor="middle" font-family="Roboto, sans-serif" font-weight="700" font-size="22" fill="#fff">$</text>
      <circle cx="44" cy="63" r="5" fill="#fff"/><circle cx="72" cy="63" r="5" fill="#fff"/>
      <path d="M32 80 Q32 70 44 70 Q56 70 56 80 Z M60 80 Q60 70 72 70 Q84 70 84 80 Z" fill="#fff"/>
    </svg>
    <h2>Operations audits</h2>
    <p>Lorem Ipsum is simply dummy text of the printing and typesetting industry. Lorem Ipsum has been the industry's standard dummy text</p>
    <a class="read-more" href="#">Read More</a>
  </article>

  <footer class="site-footer">
    <div class="copyright">Copyright &copy;&nbsp; 2014 Keyline Resource Audits</div>
    <div class="legal"><a href="#">Terms and Conditions</a> &nbsp;|&nbsp; <a href="#">Privacy policy</a></div>
  </footer>
</body>
</html>
```